Property Services Company Needs a Brochure Design

Looking for a new brochure design for an existing property services company.

We provide a range of property services from, market research, real estate brokerage, valuation and appraisal, property development and other real estate consulting services.

We would like a fresh modern brochure design with good graphics and features. Our colours are white, blue and orange.

The design should communicate, attention to detail, superior service delivery and distinction in results.
Updates

I would like the brochure to be roughly about 20 pages.

Containing the following,

1) An introduction
2) Contents Page
2) What we do
3) Our Services
4) Agency & Brokerage
5) Real Estate Consulting
6) Market Research
7) Appraisal & Valuation
8) Project Management
9) Property Development

I would also like icons to represent items 4,5,6,7,8 & 9, they should be represented vertically on each of the pages from the contents page and highlighted individually on the pages that they represent.. i.e. on appraisal & valuation page, all six icons will be arranged vertically and the appraisal and valuations icon will be highlighted.

I will also like to have images that depict the services on the various pages.

I have some pages I think will flow which I will upload shortly.

Industry/Entity Type

Real Estate

Font styles to use
Serif

Colors
f78f20
0455a3

```html
<!DOCTYPE html>
<html lang="en">
<head>
<meta charset="utf-8">
<title>Harrowgate – Brochure Spreads</title>
<link rel="stylesheet" href="https://fonts.googleapis.com/css2?family=Open+Sans:wght@300;400;600;700&display=swap">
<style>
  :root {
    --orange: #f78f20;
    --blue: #0455a3;
    --blue-deep: #0b3f80;
    --slate: #2b333d;
    --slate-light: #39424d;
    --paper: #ffffff;
    --ink: #3a3a3a;
    --backdrop: #e4e5e8;
    --label: #8a8d93;
  }
  * { box-sizing: border-box; margin: 0; padding: 0; }
  html, body { width: 1200px; height: 900px; overflow: hidden; }
  body {
    background: var(--backdrop);
    font-family: "Open Sans", Arial, sans-serif;
    color: var(--ink);
  }
  .board { position: relative; width: 1200px; height: 900px; }

  .spread-label {
    position: absolute;
    font-size: 13px;
    font-weight: 600;
    color: var(--label);
  }
  .spread {
    position: absolute;
    width: 570px;
    height: 202px;
    overflow: hidden;
    background: var(--paper);
    box-shadow: 0 3px 10px rgba(0,0,0,.25);
  }
  .spread-art { position: absolute; inset: 0; width: 570px; height: 202px; }
  .abs { position: absolute; }

  .body-copy p {
    font-size: 5.2px;
    line-height: 1.5;
    margin-bottom: 3.5px;
    color: var(--ink);
  }
  .section-title {
    font-size: 6.5px;
    font-weight: 700;
    color: #222;
    margin-bottom: 4px;
    letter-spacing: .2px;
  }

  /* cover */
  .brand {
    display: flex; align-items: center; gap: 5px;
    font-size: 16px; font-weight: 600; color: var(--blue-deep);
  }
  .brand-mark { width: 9px; height: 14px; background: var(--orange); }
  .contact-block { color: #d9dde2; }
  .contact-block h3 { font-size: 8px; font-weight: 400; margin-bottom: 5px; }
  .contact-block li { list-style: none; font-size: 5.5px; line-height: 1.4; padding-left: 16px; }

  /* contents */
  .contents-title { font-size: 5.5px; font-weight: 700; color: #222; }
  .contents-list { list-style: none; }
  .contents-list li {
    height: 16px;
    display: flex; align-items: flex-end; justify-content: flex-end;
    padding: 0 8px 2px 0;
    font-size: 7px; font-weight: 600; color: var(--paper);
    border-bottom: 0.6px solid rgba(255,255,255,.8);
  }

  /* services overview */
  .services-title { font-size: 5.5px; font-weight: 700; color: #222; }
  .service-item {
    display: flex; align-items: center; gap: 6px;
    font-size: 8.5px; font-weight: 600;
  }
  .service-item svg { width: 20px; height: 20px; flex: none; }
  .service-item.is-blue { color: var(--blue-deep); }
  .service-item.is-blue svg { color: var(--orange); }
  .service-item.is-orange { color: var(--orange); justify-content: flex-end; }
  .service-item.is-orange svg { color: var(--blue-deep); }

  /* service pages */
  .page-header {
    font-size: 9px; font-weight: 300; letter-spacing: .4px;
    color: var(--paper); text-transform: uppercase;
  }
  .icon-tile {
    display: flex; align-items: center; justify-content: center;
  }
  .align-right p { text-align: right; }
</style>
</head>
<body>
<svg width="0" height="0" style="position:absolute" aria-hidden="true">
  <defs>
    <symbol id="icon-chart" viewBox="0 0 24 24">
      <rect x="3" y="15" width="3" height="6" fill="currentColor"/>
      <rect x="8" y="12" width="3" height="9" fill="currentColor"/>
      <rect x="13" y="9" width="3" height="12" fill="currentColor"/>
      <rect x="18" y="6" width="3" height="15" fill="currentColor"/>
      <path d="M2 12 L8 7 L12 9 L20 2" fill="none" stroke="currentColor" stroke-width="1.6"/>
      <path d="M16 2 H20.5 V6.5" fill="none" stroke="currentColor" stroke-width="1.6"/>
    </symbol>
    <symbol id="icon-search-house" viewBox="0 0 24 24">
      <circle cx="10" cy="10" r="7" fill="none" stroke="currentColor" stroke-width="2"/>
      <path d="M15 15 L22 22" stroke="currentColor" stroke-width="3" stroke-linecap="round"/>
      <path d="M6 10.5 L10 7 L14 10.5 V14 H6 Z" fill="currentColor"/>
    </symbol>
    <symbol id="icon-team" viewBox="0 0 24 24">
      <circle cx="12" cy="6" r="3" fill="currentColor"/>
      <circle cx="5" cy="9" r="2.4" fill="currentColor"/>
      <circle cx="19" cy="9" r="2.4" fill="currentColor"/>
      <path d="M7.5 20 V13 Q12 9 16.5 13 V20 Z" fill="currentColor"/>
      <path d="M1.5 20 V15 Q5 12 7 14 V20 Z M22.5 20 V15 Q19 12 17 14 V20 Z" fill="currentColor"/>
    </symbol>
    <symbol id="icon-document" viewBox="0 0 24 24">
      <rect x="3" y="3" width="14" height="18" rx="1.5" fill="none" stroke="currentColor" stroke-width="1.6"/>
      <path d="M6 8 H14 M6 12 H14 M6 16 H11" stroke="currentColor" stroke-width="1.4"/>
      <circle cx="18" cy="16" r="4" fill="none" stroke="currentColor" stroke-width="1.6"/>
      <path d="M16.3 16 L17.6 17.3 L19.8 14.8" fill="none" stroke="currentColor" stroke-width="1.3"/>
    </symbol>
    <symbol id="icon-cycle" viewBox="0 0 24 24">
      <rect x="1.5" y="1.5" width="21" height="21" rx="4" fill="none" stroke="currentColor" stroke-width="1.6"/>
      <path d="M6 12 A6 6 0 0 1 17 8.5" fill="none" stroke="currentColor" stroke-width="2"/>
      <path d="M18 12 A6 6 0 0 1 7 15.5" fill="none" stroke="currentColor" stroke-width="2"/>
      <path d="M17.5 5 V9 H13.5 M6.5 19 V15 H10.5" fill="none" stroke="currentColor" stroke-width="1.6"/>
    </symbol>
    <symbol id="icon-building" viewBox="0 0 24 24">
      <path d="M3 21 V8 L10 4 V21 M10 21 V2 H20 V21 M1 21 H23" fill="none" stroke="currentColor" stroke-width="1.6"/>
      <path d="M13 6 H17 M13 10 H17 M13 14 H17 M5 11 H8 M5 15 H8" stroke="currentColor" stroke-width="1.4"/>
    </symbol>
  </defs>
</svg>

<main class="board">

  <!-- Cover -->
  <span class="spread-label" style="left:60px; top:192px;">cover back</span>
  <span class="spread-label" style="left:345px; top:192px;">cover front</span>
  <section class="spread cover-spread" style="left:20px; top:214px;">
    <svg class="spread-art" viewBox="0 0 570 202" aria-hidden="true">
      <rect width="570" height="202" fill="var(--slate)"/>
      <polygon points="150,202 285,88 285,202" fill="var(--blue-deep)"/>
      <polygon points="312,0 570,0 570,170 285,20" fill="var(--paper)"/>
      <polygon points="285,27 505,143 420,202 285,202" fill="var(--blue-deep)"/>
      <line x1="285" y1="23" x2="570" y2="173" stroke="var(--orange)" stroke-width="4"/>
      <line x1="285" y1="0" x2="285" y2="202" stroke="#1f262e" stroke-width="1"/>
    </svg>
    <div class="abs brand" style="left:410px; top:6px;">
      <span class="brand-mark"></span>Harrowgate
    </div>
    <div class="abs contact-block" style="left:14px; top:128px;">
      <h3>Contact information</h3>
      <ul>
        <li>Adress</li>
        <li>Phone</li>
        <li>email adress</li>
        <li>web adress</li>
      </ul>
    </div>
  </section>

  <!-- Page 3-4 -->
  <span class="spread-label" style="left:900px; top:192px;">page 3-4</span>
  <section class="spread services-spread" style="left:610px; top:214px;">
    <svg class="spread-art" viewBox="0 0 570 202" aria-hidden="true">
      <rect width="570" height="202" fill="var(--paper)"/>
      <line x1="8" y1="12" x2="8" y2="202" stroke="var(--orange)" stroke-width="1.5"/>
      <polygon points="0,196 570,160 570,202 0,202" fill="var(--blue-deep)"/>
      <line x1="0" y1="194" x2="570" y2="158" stroke="var(--orange)" stroke-width="2.5"/>
      <line x1="285" y1="0" x2="285" y2="202" stroke="#e6e6e6" stroke-width="1"/>
    </svg>
    <div class="abs body-copy" style="left:16px; top:14px; width:250px;">
      <h2 class="section-title">WHAT WE DO</h2>
      <p>Harrowgate is a leading property services company, incorporated in 1984, providing bespoke solutions in advisory, brokerage and turnkey solutions to owners, occupiers and property investors. Over the years we have expanded our services with a foundation based on core strengths, unrivalled local expertise, network and knowledge combined with strategic partnership. As well as providing property solutions we also develop commercial and residential units.</p>
      <p>Our growth has been based on maintaining relationships with our extensive client base, ranging from financial institutions, government agencies, airlines and servicing companies, manufacturing companies, multinationals and local corporations, to private developers and investors. Our team knows the local market inside and out, giving clear advice for all property needs.</p>
      <p>We offer a superior end to end solution: our market research is a core component, and our advice is based on accurate, current information, allowing our clients to maximise their investment on the sale or lease of property.</p>
      <p>We aim to exceed our clients' requirements, delivering distinction in results.</p>
    </div>
    <h2 class="abs services-title" style="right:10px; top:8px;">OUR SERVICES</h2>
    <div class="abs service-item is-blue" style="left:298px; top:34px;"><svg><use href="#icon-chart"/></svg>Agency &amp; Brokerage</div>
    <div class="abs service-item is-blue" style="left:298px; top:74px;"><svg><use href="#icon-search-house"/></svg>Real Estate Consulting</div>
    <div class="abs service-item is-blue" style="left:298px; top:114px;"><svg><use href="#icon-team"/></svg>Market Research</div>
    <div class="abs service-item is-orange" style="right:8px; top:26px;">Appraisal &amp; Valuation<svg><use href="#icon-document"/></svg></div>
    <div class="abs service-item is-orange" style="right:8px; top:66px;">Project Management<svg><use href="#icon-cycle"/></svg></div>
    <div class="abs service-item is-orange" style="right:8px; top:106px;">Property Development<svg><use href="#icon-building"/></svg></div>
  </section>

  <!-- Page 1-2 -->
  <span class="spread-label" style="left:210px; top:472px;">page 1-2</span>
  <section class="spread intro-spread" style="left:20px; top:494px;">
    <svg class="spread-art" viewBox="0 0 570 202">
      <rect width="570" height="202" fill="var(--paper)"/>
      <polygon points="0,160 0,202 26,202" fill="var(--blue-deep)" aria-hidden="true"/>
      <polygon points="215,0 318,0 262,38" fill="var(--blue-deep)" aria-hidden="true"/>
      <defs>
        <linearGradient id="grad-portrait" x1="0" y1="0" x2="1" y2="1">
          <stop offset="0" stop-color="#e9e7e2"/>
          <stop offset=".55" stop-color="#8b7a6c"/>
          <stop offset="1" stop-color="#2f3c57"/>
        </linearGradient>
        <linearGradient id="grad-office" x1="0" y1="0" x2="1" y2="1">
          <stop offset="0" stop-color="#f2f2f2"/>
          <stop offset="1" stop-color="#8e9094"/>
        </linearGradient>
      </defs>
      <polygon points="205,62 318,10 445,202 205,202" fill="url(#grad-portrait)" role="img" aria-label="Photo of a smiling businessman reviewing documents"/>
      <polygon points="329,22 570,22 570,175 427,175" fill="var(--orange)" aria-hidden="true"/>
      <polygon points="427,178 570,178 570,202 443,202" fill="var(--blue-deep)" aria-hidden="true"/>
      <line x1="315" y1="0" x2="445" y2="202" stroke="var(--orange)" stroke-width="3" aria-hidden="true"/>
      <line x1="285" y1="0" x2="285" y2="202" stroke="#e6e6e6" stroke-width="1" aria-hidden="true"/>
    </svg>
    <div class="abs body-copy" style="left:12px; top:24px; width:190px;">
      <h2 class="section-title">INTRODUCTION</h2>
      <p>HARROWGATE was incorporated in 1984 as an interior design and property development company. Over the years we have expanded our service with a foundation based on core strengths, unrivalled local expertise, network and knowledge combined with strategic partnerships.</p>
      <p>Harrowgate offers a comprehensive range of services on a local, regional, national and international basis to tenants, owners, and investors within the residential and commercial property market.</p>
      <p>Our clients depend on our ability to draw on years of experience in the local market, our professionals know their communities and the property market inside and out, and provide knowledgeable, creative solutions to all their real estate needs.</p>
      <p>We currently provide services to corporations, financial institutions, government agencies, public sector entities, developers and investors. Our knowledge, expertise, experience and technological resources allow us to be a superior service provider.</p>
    </div>
    <h2 class="abs contents-title" style="left:480px; top:8px;">CONTENT</h2>
    <ul class="abs contents-list" style="left:330px; top:24px; width:240px;">
      <li>What we do</li>
      <li>Our Services</li>
      <li>Agency &amp; Brokerage</li>
      <li>Real Estate Consulting</li>
      <li>Market Research</li>
      <li>Appraisal &amp; Valuation</li>
      <li>Project Management</li>
      <li>Property Development</li>
    </ul>
  </section>

  <!-- Page 5-6 -->
  <span class="spread-label" style="left:880px; top:472px;">page 5-6</span>
  <section class="spread detail-spread" style="left:610px; top:494px;">
    <svg class="spread-art" viewBox="0 0 570 202">
      <rect width="570" height="202" fill="var(--paper)"/>
      <polygon points="0,0 120,0 0,70" fill="var(--blue-deep)" aria-hidden="true"/>
      <rect x="60" y="8" width="225" height="27" fill="var(--orange)" aria-hidden="true"/>
      <polygon points="0,170 0,202 20,202" fill="var(--blue-deep)" aria-hidden="true"/>
      <polygon points="285,0 335,0 335,38 285,76" fill="var(--blue-deep)" aria-hidden="true"/>
      <rect x="335" y="8" width="235" height="28" fill="var(--orange)" aria-hidden="true"/>
      <polygon points="285,78 335,40 470,202 285,202" fill="url(#grad-office)" role="img" aria-label="Photo of a modern office with a desk chair"/>
      <line x1="335" y1="37" x2="472" y2="202" stroke="var(--orange)" stroke-width="3" aria-hidden="true"/>
      <polygon points="478,202 570,165 570,202" fill="var(--blue-deep)" aria-hidden="true"/>
      <line x1="285" y1="0" x2="285" y2="202" stroke="#e6e6e6" stroke-width="1" aria-hidden="true"/>
    </svg>
    <h2 class="abs page-header" style="right:296px; top:15px;">Agency &amp; Brokerage</h2>
    <div class="abs icon-tile" style="left:22px; top:30px; width:62px; height:58px; background:var(--orange); color:var(--paper);">
      <svg width="38" height="38" aria-hidden="true"><use href="#icon-chart"/></svg>
    </div>
    <div class="abs body-copy" style="left:22px; top:100px; width:250px;">
      <p>The brokerage team, covers both landlords and tenants across the residential and commercial markets. With a large database of industry specific individuals and corporate clients twinned with a large database of inventory, we are able to very quickly understand the needs of our clients and find the perfect fit. We enjoy long standing relationships with many of our clients and landlords, and are always happy to advise on how best to maximize their rental income.</p>
    </div>
    <h2 class="abs page-header" style="left:345px; top:15px;">Real Estate Consulting</h2>
    <div class="abs icon-tile" style="left:522px; top:2px; width:40px; height:40px; background:var(--paper); color:var(--orange);">
      <svg width="28" height="28" aria-hidden="true"><use href="#icon-search-house"/></svg>
    </div>
    <div class="abs body-copy align-right" style="left:400px; top:56px; width:160px;">
      <p>We provide a broad range of consulting services. We understand that our client needs may vary and our experienced team are at hand to provide tailored solutions to their needs. Our professional services include corporate property strategy, feasibility studies, market studies, due diligence, property tax advice, portfolio and asset review and foreign direct investment advice.</p>
    </div>
  </section>

</main>
</body>
</html>
```